BRELWINCare.co.uk - Mental Health Clinic for Child and Adolescents

Updated 29/01/2018***
I am not sure you guys are getting the idea regards to the opening page / homescreen layout. Can you look at the new images I have uploaded (page 5, 6 and 7) These are some of the layouts I like but to incorporate my chosen images, with the BRELWIN commissioner, buttons and a sliding header bar.
I have written a strong brief, I am looking for a website, preferably wordpress as i know they are easy to maintain. I am looking for a one page site, with the top / opening page being full screen image with drop down categories. I have made a rough design, see full brief in word doc attached, there is some freedom to play around with the design aspect but it will need to relay all the content provided. I like a minimal feel. I have also attached some images that may be useful, but will need a new logo for BRELWIN Care. I have attached some logo idea's, it is up to you decide whether you want to use them.
I would prefer the homepage as full screen image, and the categories offered as a drop down or over the main image.
I have also attached linked to some competitors websites:
https://www.vorimant-health.co.uk/
http://www.qlbn.org.uk/
Industry/Entity Type
Clinic
Number of Pages Required
1 page
Font styles to use
Look and feel
Each slider illustrates characteristics of the customer's brand and the style your logo design should communicate.

```html
<!DOCTYPE html>
<html lang="en">
<head>
<meta charset="utf-8">
<title>BRELWIN Care – Services</title>
<link rel="stylesheet" href="https://fonts.googleapis.com/css2?family=Open+Sans:wght@400;600;700&family=Poppins:wght@400&family=Yellowtail&display=swap">
<style>
  :root {
    --panel-bg: #f1f0ef;
    --white: #ffffff;
    --teal: #0f9a84;
    --purple: #5c1b63;
    --ink: #222222;
    --ink-soft: #333333;
    --title-ink: #1c0f14;
    --rule: #dcdcdc;
    --icon: #2b2b2b;
  }
  * { box-sizing: border-box; margin: 0; padding: 0; }
  html, body { width: 1200px; height: 1200px; overflow: hidden; background: var(--white); }
  body { position: relative; font-family: "Open Sans", Arial, sans-serif; color: var(--ink); }

  .page {
    position: absolute; left: 0; width: 1200px; height: 592px;
    background: var(--panel-bg); overflow: hidden;
  }
  .page--adhd { top: 0; }
  .page--commissioners { top: 600px; }

  .brand {
    position: absolute; left: 0; top: 0; width: 165px; height: 84px;
    background: var(--white); padding: 20px 0 0 18px; z-index: 2;
  }
  .brand__name {
    display: flex; align-items: center; gap: 7px;
    font-family: "Open Sans", Arial, sans-serif; font-weight: 700;
    font-size: 23px; letter-spacing: 0.5px; color: var(--purple); line-height: 1;
  }
  .brand__mark { width: 12px; height: 12px; border-radius: 50%; background: var(--teal); }
  .brand__tagline {
    margin-top: 8px; font-size: 10px; font-weight: 600; color: var(--purple); letter-spacing: 0.1px;
  }

  .sidenav {
    position: absolute; left: 0; top: 84px; width: 76px; height: 508px; background: var(--white);
  }
  .sidenav__item {
    position: absolute; left: 12px; width: 64px; display: flex; align-items: center; justify-content: center;
    color: var(--icon); border-bottom: 1px solid var(--rule);
  }
  .sidenav__item svg { width: 30px; height: 30px; }
  .sidenav__item--menu { top: 0; height: 87px; }
  .sidenav__item--forms { top: 87px; height: 74px; }
  .sidenav__item--team { top: 161px; height: 74px; }
  .sidenav__item--services { top: 235px; height: 74px; }
  .sidenav__item--contact { top: 309px; height: 87px; }
  .sidenav__item--news { top: 396px; height: 78px; }

  .sidenav__item--active {
    width: 153px; background: var(--teal); color: var(--white); border-bottom: none;
    border-right: 3px solid #1b1b1b; justify-content: flex-start; padding-left: 16px; gap: 22px;
  }
  .sidenav__label { font-size: 15px; font-weight: 400; letter-spacing: 0.3px; }

  .content { position: absolute; left: 254px; width: 560px; }
  .content__title {
    font-family: "Yellowtail", "Brush Script MT", cursive; font-weight: 400; color: var(--title-ink);
    font-size: 60px; line-height: 1; letter-spacing: 0.5px;
  }
  .page--adhd .content { top: 52px; }
  .page--commissioners .content { top: 112px; }
  .page--commissioners .content__title { font-size: 56px; }

  .content__body {
    font-size: 13.6px; line-height: 28.8px; color: var(--ink-soft);
    hyphens: manual; -webkit-hyphens: manual; letter-spacing: -0.05px;
  }
  .page--adhd .content__body { margin-top: 20px; }
  .page--commissioners .content__body { margin-top: 28px; }

  .services { margin-top: 28px; font-size: 13.6px; color: var(--ink-soft); }
  .services__list { list-style: none; }
  .services__list li { line-height: 28.8px; position: relative; padding-left: 27px; }
  .services__list li::before { content: "•"; position: absolute; left: 0; font-size: 11px; }
  .services__intro { line-height: 28.8px; }

  .hero-photo { position: absolute; left: 820px; top: 0; width: 380px; height: 592px; }

  .footer-note {
    position: absolute; left: 0; width: 1200px; text-align: center; padding-left: 12px;
    font-family: "Poppins", Arial, sans-serif; font-size: 11.5px; color: var(--ink);
  }
  .page--adhd .footer-note { top: 560px; }
  .page--commissioners .footer-note { top: 561px; }
</style>
</head>
<body>

<svg width="0" height="0" style="position:absolute">
  <defs>
    <symbol id="icon-menu" viewBox="0 0 30 30"><g stroke="currentColor" stroke-width="2" fill="none"><line x1="3" y1="7" x2="27" y2="7"/><line x1="3" y1="15" x2="27" y2="15"/><line x1="3" y1="23" x2="27" y2="23"/></g></symbol>
    <symbol id="icon-forms" viewBox="0 0 30 30"><g stroke="currentColor" stroke-width="1.3" fill="none"><rect x="4" y="5" width="20" height="23" rx="1"/><line x1="4" y1="8" x2="24" y2="8"/><line x1="7" y1="12" x2="16" y2="12"/><line x1="7" y1="16" x2="14" y2="16"/><line x1="7" y1="20" x2="12" y2="20"/><path d="M26 9 L15 22 L13 26 L17 24 L28 11 Z"/></g></symbol>
    <symbol id="icon-team" viewBox="0 0 30 30"><g stroke="currentColor" stroke-width="1.3" fill="none"><circle cx="15" cy="10" r="5"/><path d="M7 27 C7 19 23 19 23 27"/><circle cx="6" cy="14" r="3.2"/><path d="M1 27 C1 21 8 20 9 22"/><circle cx="24" cy="14" r="3.2"/><path d="M29 27 C29 21 22 20 21 22"/></g></symbol>
    <symbol id="icon-services" viewBox="0 0 30 30"><g stroke="currentColor" stroke-width="1.3" fill="none"><path d="M5 22 L21 6 L24 9 L8 25 L4 26 Z"/><path d="M6 5 L25 24 L22 27 L3 8 Z"/><line x1="9" y1="11" x2="11" y2="9"/><line x1="13" y1="15" x2="15" y2="13"/><line x1="17" y1="19" x2="19" y2="17"/></g></symbol>
    <symbol id="icon-phone" viewBox="0 0 30 30"><path d="M8 4 L12 10 L9 13 C11 17 13 19 17 21 L20 18 L26 22 L23 26 C14 26 4 16 4 7 Z" stroke="currentColor" stroke-width="1.4" fill="none" stroke-linejoin="round"/></symbol>
    <symbol id="icon-news" viewBox="0 0 30 30"><g stroke="currentColor" stroke-width="1.3" fill="none"><rect x="2" y="4" width="26" height="22"/><line x1="2" y1="9" x2="28" y2="9"/><line x1="5" y1="13" x2="25" y2="13"/><rect x="5" y="16" width="6" height="6"/><line x1="14" y1="17" x2="25" y2="17"/><line x1="14" y1="21" x2="25" y2="21"/></g></symbol>
  </defs>
</svg>

<section class="page page--adhd">
  <svg class="hero-photo" viewBox="820 0 380 592" role="img" aria-label="Photo of three smiling teenage friends sitting together on a sofa">
    <defs>
      <linearGradient id="adhd-photo-fill" x1="0" y1="0" x2="1" y2="1">
        <stop offset="0" stop-color="#e7e4e0"/>
        <stop offset="0.45" stop-color="#b9a996"/>
        <stop offset="0.75" stop-color="#6f8398"/>
        <stop offset="1" stop-color="#a7b7c6"/>
      </linearGradient>
    </defs>
    <path d="M1200 60 L862 124 Q828 132 838 166 L938 470 L1200 560 Z" fill="url(#adhd-photo-fill)"/>
    <path d="M1200 60 L862 124 Q828 132 838 166 L938 470" fill="none" stroke="var(--teal)" stroke-width="6"/>
  </svg>

  <div class="brand">
    <div class="brand__name"><span class="brand__mark"></span>BRELWIN</div>
    <div class="brand__tagline">Care for Growing Minds</div>
  </div>

  <nav class="sidenav">
    <a class="sidenav__item sidenav__item--menu"><svg><use href="#icon-menu"/></svg></a>
    <a class="sidenav__item sidenav__item--forms"><svg><use href="#icon-forms"/></svg></a>
    <a class="sidenav__item sidenav__item--team"><svg><use href="#icon-team"/></svg></a>
    <a class="sidenav__item sidenav__item--services sidenav__item--active"><svg><use href="#icon-services"/></svg><span class="sidenav__label">SERVICES</span></a>
    <a class="sidenav__item sidenav__item--contact"><svg><use href="#icon-phone"/></svg></a>
    <a class="sidenav__item sidenav__item--news"><svg><use href="#icon-news"/></svg></a>
  </nav>

  <main class="content">
    <h1 class="content__title">Adhd</h1>
    <p class="content__body">We have a multidisciplinaryteam that has been selected due to their vast experience and reputation of being some of the best in their field. The team consists of a Clinical Psy&shy;chologist, Consultant Psychiatrist and Nurse who will work collaboratively to provide a robust, thorough and highly accurate assessment.&nbsp; Should your child need post treat&shy;ment, we will recommend and offer support that is best suited to the child and family.</p>
    <div class="services">
      <p class="services__intro">Services offered are:</p>
      <ul class="services__list">
        <li>Service 1</li>
        <li>Service 2</li>
        <li>Service 3</li>
        <li>Service 4</li>
        <li>Service 5</li>
        <li>Service 6</li>
      </ul>
    </div>
  </main>

  <p class="footer-note">© 2018 All Rights Reserved.brelwincare.co.uk</p>
</section>

<section class="page page--commissioners">
  <svg class="hero-photo" viewBox="820 0 380 592" role="img" aria-label="Photo of a smiling young girl in a striped top sitting on a sofa">
    <defs>
      <linearGradient id="comm-photo-fill" x1="0" y1="0" x2="1" y2="1">
        <stop offset="0" stop-color="#d9d6cf"/>
        <stop offset="0.5" stop-color="#b7a692"/>
        <stop offset="0.8" stop-color="#8c7a68"/>
        <stop offset="1" stop-color="#a9b3b6"/>
      </linearGradient>
    </defs>
    <path d="M1200 60 L860 126 Q826 134 836 168 L932 440 L1200 556 Z" fill="url(#comm-photo-fill)"/>
    <path d="M1200 60 L860 126 Q826 134 836 168 L932 440" fill="none" stroke="var(--teal)" stroke-width="6"/>
  </svg>

  <div class="brand">
    <div class="brand__name"><span class="brand__mark"></span>BRELWIN</div>
    <div class="brand__tagline">Care for Growing Minds</div>
  </div>

  <nav class="sidenav">
    <a class="sidenav__item sidenav__item--menu"><svg><use href="#icon-menu"/></svg></a>
    <a class="sidenav__item sidenav__item--forms"><svg><use href="#icon-forms"/></svg></a>
    <a class="sidenav__item sidenav__item--team"><svg><use href="#icon-team"/></svg></a>
    <a class="sidenav__item sidenav__item--services"><svg><use href="#icon-services"/></svg></a>
    <a class="sidenav__item sidenav__item--contact"><svg><use href="#icon-phone"/></svg></a>
    <a class="sidenav__item sidenav__item--news"><svg><use href="#icon-news"/></svg></a>
  </nav>

  <main class="content">
    <h1 class="content__title">Commissioners</h1>
    <p class="content__body">Are you looking to reduce waiting times or commission part of your ADHD or ASD path&shy;way?&nbsp; We have a proven track record in providing robust, high quality, patient focused assessment and post-assessment treatment.&nbsp; We can come take referrals at a variety of stages and are able to offer the highest levels of service and exceptional value.<br>Call us today to discuss how we can be supporting part of your service.</p>
  </main>

  <p class="footer-note">© 2018 All Rights Reserved.brelwincare.co.uk</p>
</section>

</body>
</html>
```